Hvac and insulation company needs good looking business card design

We are hvac and insulation company and looking for a new business cards that look to today standards designs

Target Market(s)

homeowners

Industry/Entity Type

Hvac

Contact Information for Business Card

Name: Walter Brinoku
Home comfort consultant
address: 4827 Dunmore St #215 Oakland, CA 94619
office: 888-316-2790
cell: 510-742-3185
Lic.# 584261
Email: walter@corvane-hvac.com
Web: corvane-hvac.com

Requirements
Must have
• clean and sleek look
Nice to have
• simple with a clean look
Should not have
• to busy business card

```html
<!DOCTYPE html>
<html lang="en">
<head>
<meta charset="utf-8">
<title>Corvane Home Solutions – Business Card</title>
<link rel="stylesheet" href="https://fonts.googleapis.com/css2?family=Open+Sans:wght@400;600;700&display=swap">
<style>
  :root {
    --backdrop: #2b2522;
    --card: #0b0b0b;
    --card-edge: #161616;
    --accent: #f08a1c;
    --ink: #f2f2f2;
    --ink-soft: #d6d6d6;
    --flash: #ffffff;
  }
  * { margin: 0; padding: 0; box-sizing: border-box; }
  html, body {
    width: 1200px;
    height: 842px;
    overflow: hidden;
    background: var(--backdrop);
    font-family: "Open Sans", Arial, sans-serif;
  }
  .canvas {
    position: relative;
    width: 1200px;
    height: 842px;
  }
  .card {
    position: absolute;
    top: 271px;
    width: 520px;
    height: 300px;
    background: linear-gradient(135deg, var(--card-edge), var(--card) 60%);
    overflow: hidden;
    box-shadow: 0 10px 30px rgba(0,0,0,.5);
  }
  .card--contact { left: 50px; }
  .card--brand { left: 630px; }

  /* contact side */
  .band {
    position: absolute;
    left: 0;
    width: 100%;
    background: var(--accent);
  }
  .band--top { top: 16px; height: 7px; }
  .band--bottom { bottom: 18px; height: 12px; }

  .contact {
    position: absolute;
    left: 120px;
    top: 62px;
    width: 300px;
    color: var(--ink);
  }
  .contact__name {
    font-weight: 700;
    font-size: 15px;
    letter-spacing: .3px;
    text-transform: uppercase;
  }
  .contact__role {
    font-size: 12px;
    color: var(--ink-soft);
    margin-top: 2px;
  }
  .contact__lines {
    margin-top: 18px;
    text-align: center;
    font-size: 12.5px;
    line-height: 1.35;
    width: 210px;
  }
  .contact__address {
    margin-top: 24px;
    font-size: 12.5px;
    text-align: center;
    width: 260px;
    margin-left: -30px;
  }
  .contact__license {
    margin-top: 6px;
    font-size: 12.5px;
    text-align: center;
    width: 210px;
  }

  /* brand side */
  .tab {
    position: absolute;
    width: 24px;
    height: 40px;
    background: var(--accent);
    border-right: 5px solid var(--flash);
  }
  .tab--left { left: 44px; top: 160px; }
  .tab--right { right: 44px; top: 22px; }

  .brand {
    position: absolute;
    left: 0;
    right: 0;
    top: 50%;
    transform: translateY(-50%);
    display: flex;
    align-items: center;
    justify-content: center;
    gap: 12px;
  }
  .brand__mark {
    width: 18px;
    height: 18px;
    background: var(--accent);
  }
  .brand__name {
    color: var(--accent);
    font-weight: 600;
    font-size: 30px;
    letter-spacing: .5px;
  }
</style>
</head>
<body>
  <main class="canvas">
    <section class="card card--contact" aria-label="Contact side">
      <div class="band band--top"></div>
      <div class="contact">
        <p class="contact__name">Walter Brinoku</p>
        <p class="contact__role">Home Comfort Consultant</p>
        <div class="contact__lines">
          <p>888-316-2790</p>
          <p>510-742-3185</p>
          <p>walter@corvane-hvac.com</p>
          <p>corvane-hvac.com</p>
        </div>
        <p class="contact__address">4827 Dunmore St #215 Oakland, CA 94619</p>
        <p class="contact__license">Lic.# 584261</p>
      </div>
      <div class="band band--bottom"></div>
    </section>

    <section class="card card--brand" aria-label="Brand side">
      <div class="tab tab--right"></div>
      <div class="tab tab--left"></div>
      <div class="brand">
        <span class="brand__mark"></span>
        <span class="brand__name">Corvane Home Solutions</span>
      </div>
    </section>
  </main>
</body>
</html>
```